Business card for my new company (Accounting firm)

I need a business card for my new business Brightwell Advisory and Ledger SA. Our services are accounting, tax, audit and financial management. Our customers are small companies, start-ups and new companies. The final design has to show financial security, trust and growth. Please find our logo attached to the business card. Text for the business card: Brightwell Advisory and Ledger SA Tomas Varenholt Director and Founder Certified Accountant Tel. 022 418 57 34 tv@clairevalconseil.ch www.clairevalconseil.ch Rue des Vergières 27 1201 Geneva
Target Market(s)
Our customers are small companies, start-ups and new companies.
Industry/Entity Type
Finance And Accounting
Contact Information for Business Card
Claireval Conseil et Comptes SA
Tomas Varenholt
Directeur et Fondateur
Expert-comptable diplômé
Tél. 022 418 57 34
tv@clairevalconseil.ch
www.clairevalconseil.ch
Rue des Vergières 27
1201 Genève

```html
<!DOCTYPE html>
<html lang="fr">
<head>
<meta charset="utf-8">
<title>Claireval Conseil et Comptes SA – Carte de visite</title>
<link href="https://fonts.googleapis.com/css2?family=Montserrat:wght@500;700&family=Lato:wght@400&display=swap" rel="stylesheet">
<style>
  :root {
    --bg: #2b2b2e;
    --blue-deep: #1a68a3;
    --blue-mid: #2190cf;
    --blue-light: #28b1e1;
    --ink: #3a3a3c;
    --rule: #8a8a8a;
    --paper: #ffffff;
  }
  * { margin: 0; padding: 0; box-sizing: border-box; }
  html, body { width: 1200px; height: 823px; overflow: hidden; background: var(--bg); }
  .canvas { position: relative; width: 1200px; height: 823px; }

  .card {
    position: absolute;
    top: 262px;
    width: 520px;
    height: 300px;
    overflow: hidden;
    box-shadow: 0 10px 24px rgba(0,0,0,.45);
  }

  /* Front */
  .card-front {
    left: 60px;
    background: linear-gradient(35deg, var(--blue-deep) 0%, var(--blue-mid) 55%, var(--blue-light) 100%);
    display: flex; align-items: center; justify-content: center;
  }
  .brand {
    display: flex; align-items: center; gap: 12px;
    font-family: "Montserrat", sans-serif; font-weight: 700;
  }
  .brand-square { width: 22px; height: 22px; }
  .brand-name { font-size: 30px; letter-spacing: 1px; line-height: 1; }
  .card-front .brand { color: var(--paper); }
  .card-front .brand-square { background: var(--paper); }

  /* Back */
  .card-back { left: 620px; background: var(--paper); }
  .card-back::after {
    content: ""; position: absolute; left: 0; right: 0; bottom: 0; height: 8px;
    background: linear-gradient(90deg, var(--blue-deep), var(--blue-light));
  }
  .logo-zone {
    position: absolute; left: 0; top: 0; width: 240px; height: 292px;
    display: flex; align-items: center; justify-content: center;
  }
  .card-back .brand { flex-direction: column; gap: 8px; color: var(--blue-mid); }
  .card-back .brand-square { background: var(--blue-mid); width: 26px; height: 26px; }
  .card-back .brand-name { font-size: 26px; }
  .card-back .brand-sub { font-size: 12px; letter-spacing: 1.5px; text-transform: uppercase; }

  .divider {
    position: absolute; left: 246px; top: 58px; width: 1px; height: 176px; background: var(--rule);
  }
  .details {
    position: absolute; left: 264px; top: 52px; right: 18px;
    font-family: "Lato", sans-serif; color: var(--ink); font-size: 12.5px; line-height: 1.35;
  }
  .person-name {
    font-family: "Montserrat", sans-serif; font-weight: 700; color: var(--blue-mid);
    font-size: 17px; text-transform: uppercase; letter-spacing: .3px; margin-bottom: 2px;
  }
  .block { margin-bottom: 10px; }
  .contact-line { display: flex; align-items: center; gap: 8px; }
  .contact-line svg { width: 12px; height: 12px; flex: none; }
</style>
</head>
<body>
<main class="canvas">
  <section class="card card-front">
    <div class="brand">
      <span class="brand-square"></span>
      <span class="brand-name">CLAIREVAL</span>
    </div>
  </section>

  <section class="card card-back">
    <div class="logo-zone">
      <div class="brand">
        <span class="brand-square"></span>
        <span class="brand-name">CLAIREVAL</span>
        <span class="brand-sub">Conseil et Comptes</span>
      </div>
    </div>
    <div class="divider"></div>
    <div class="details">
      <p class="person-name">Tomas Varenholt</p>
      <div class="block">
        <p>Directeur et Fondateur</p>
        <p>Expert-comptable diplômé</p>
      </div>
      <div class="block">
        <p>Claireval Conseil et Comptes SA</p>
        <p>Rue des Vergières 27</p>
        <p>1201 Genève</p>
      </div>
      <p class="contact-line">
        <svg viewBox="0 0 24 24" aria-hidden="true"><path fill="#2190cf" d="M6.6 10.8a15 15 0 0 0 6.6 6.6l2.2-2.2c.3-.3.7-.4 1-.2 1.1.4 2.3.6 3.6.6.6 0 1 .4 1 1V20c0 .6-.4 1-1 1A17 17 0 0 1 3 4c0-.6.4-1 1-1h3.5c.6 0 1 .4 1 1 0 1.3.2 2.5.6 3.6.1.3 0 .7-.2 1z"/></svg>
        022 418 57 34
      </p>
      <p class="contact-line">
        <svg viewBox="0 0 24 24" aria-hidden="true"><rect x="3" y="5" width="18" height="14" fill="none" stroke="#2190cf" stroke-width="2"/><path d="M3 6l9 7 9-7" fill="none" stroke="#2190cf" stroke-width="2"/></svg>
        tv@clairevalconseil.ch
      </p>
      <p class="contact-line">
        <svg viewBox="0 0 24 24" aria-hidden="true"><circle cx="12" cy="12" r="9" fill="none" stroke="#2190cf" stroke-width="2"/><path d="M3 12h18M12 3c3 3 3 15 0 18M12 3c-3 3-3 15 0 18" fill="none" stroke="#2190cf" stroke-width="1.6"/></svg>
        www.clairevalconseil.ch
      </p>
    </div>
  </section>
</main>
</body>
</html>
```